Wordpress Design for a Private Label BBQ Brand

For our new brand, we'd need a new Wordpress website. We'd prefer to run the website on Wordpress

We'd like to include the following
- space for description of the brand
- space for product portfolio (not a shop!)
- space for socials
- space for support
- space for contact

```html
<!DOCTYPE html>
<html lang="en">
<head>
<meta charset="utf-8">
<title>Brasavo – Grill Tools</title>
<link href="https://fonts.googleapis.com/css2?family=Outfit:wght@400;500;600&family=Lato:wght@400;700&display=swap" rel="stylesheet">
<style>
:root{
  --orange:#ee6a24;
  --red:#c8202c;
  --deep-red:#a81b2a;
  --blue:#3d7fc4;
  --navy:#23489b;
  --ink:#222;
  --body:#444;
  --muted:#9a9a9a;
  --white:#fff;
  --grad:linear-gradient(90deg,#ef6b22 0%,#d8352a 60%,#b71d2c 100%);
}
*{box-sizing:border-box;margin:0;padding:0}
html,body{width:1200px;height:3710px;overflow:hidden}
body{position:relative;background:var(--white);font-family:"Lato",sans-serif;color:var(--body)}
.abs{position:absolute}
.heading{font-family:"Outfit",sans-serif;font-weight:500}
.btn{position:absolute;display:flex;align-items:center;justify-content:center;border-radius:30px;font-family:"Lato",sans-serif;font-weight:700;font-size:15px;color:var(--white);background:linear-gradient(90deg,#ef6b22,#d3302a);letter-spacing:.2px}

/* header */
.site-header{left:0;top:0;width:1200px;height:96px;background:var(--white)}
.brand{display:flex;align-items:center;gap:10px;font-family:"Outfit",sans-serif;font-weight:600;color:var(--ink)}
.brand-dot{border-radius:50%;background:var(--orange)}
.site-header .brand{left:110px;top:24px;font-size:40px;letter-spacing:1px}
.site-header .brand-dot{width:32px;height:32px}
.main-nav{left:410px;top:40px;display:flex;gap:36px;font-size:15px;color:#444}
.main-nav .active{color:var(--orange)}
.cart{left:1012px;top:42px;width:20px;height:16px}
.cart-count{left:1025px;top:28px;font-size:9px;color:#666}
.sep{left:1046px;top:42px;width:1px;height:18px;background:#ccc}
.search{left:1068px;top:42px}

/* hero */
.hero{left:0;top:96px;width:1200px;height:600px;background:radial-gradient(ellipse at 55% 70%,#e2621f 0%,#8a2d12 22%,#2a2b2c 52%,#141617 100%);clip-path:polygon(0 0,100% 0,100% 96%,92% 98%,85% 96.5%,72% 98.5%,60% 97%,48% 99%,35% 97%,22% 98.5%,10% 97%,4% 99%,0 97.5%)}
.hero-welcome{left:113px;top:170px;font-size:34px;color:#d8292c}
.hero-title{left:110px;top:212px;font-size:96px;font-weight:600;color:var(--orange);line-height:1}
.hero .btn{}
.hero-btn{left:113px;top:342px;width:145px;height:50px}

/* about */
.about-ring{left:116px;top:786px;width:408px;height:408px;border-radius:50%;border:2px solid var(--blue);border-top-color:var(--orange);border-right-color:var(--orange)}
.about-photo{left:128px;top:796px;width:384px;height:384px;border-radius:50%;background:radial-gradient(circle at 40% 35%,#d8c79a 0%,#7c9a4a 45%,#3e5a26 100%)}
.about-title{left:597px;top:800px;font-size:46px;color:var(--blue)}
.about-text{left:597px;top:880px;width:488px;font-size:15.5px;line-height:25.7px;text-align:justify;color:#333}
.about-btn{left:594px;top:1094px;width:144px;height:52px}

/* portfolio */
.portfolio{left:0;top:1282px;width:1200px;height:888px;background:linear-gradient(100deg,#ee6a22 0%,#e0452a 45%,#c62a2c 75%,#a81b2a 100%);clip-path:polygon(0 1.5%,6% 0,14% 1.2%,26% .3%,40% 1.4%,55% .2%,70% 1.3%,84% .4%,100% 1.2%,100% 98.5%,90% 99.6%,76% 98.6%,60% 99.8%,45% 98.7%,30% 99.7%,15% 98.8%,5% 99.8%,0 98.8%)}
.portfolio-title{left:0;top:1372px;width:1200px;text-align:center;font-size:44px;color:var(--white)}
.tile{position:absolute;width:307px;height:247px;background:var(--white);border:3px solid var(--navy)}
.tile-img{position:absolute;inset:30px 30px;border-radius:6px}
.tool-silver{background:linear-gradient(135deg,#e9ecef,#9aa2aa)}
.tool-dark{background:linear-gradient(135deg,#5a5e62,#1e2023)}
.view-btn{left:529px;top:2031px;width:142px;height:52px;background:var(--navy)}

/* socials */
.socials-title{left:0;top:2246px;width:1200px;text-align:center;font-size:44px;color:var(--blue)}
.post{position:absolute;top:2333px;width:236px}
.post-img{height:187px}
.post-icon{width:18px;height:18px;margin:20px auto 0;border-radius:50%;border:2px solid var(--orange)}
.post-icon.filled{background:var(--orange);border:none}
.post-name{margin-top:12px;text-align:center;font-weight:700;font-size:14.5px;color:var(--ink)}
.post-text{margin-top:7px;text-align:center;font-size:13px;line-height:21px;color:#333}
.post-meta{margin-top:14px;display:flex;justify-content:space-between;align-items:center;padding:0 16px}
.avatar{width:36px;height:36px;border-radius:50%;background:linear-gradient(135deg,#c9b29a,#7c6650)}
.ago{font-size:13px;color:var(--muted)}

/* support */
.support{left:0;top:2786px;width:1200px;height:556px;background:linear-gradient(90deg,#ef6b22 0%,#e04a28 45%,#cc2a2c 75%,#c01f2c 100%);clip-path:polygon(0 1.8%,7% .3%,18% 1.6%,32% .4%,48% 1.7%,62% .3%,78% 1.5%,90% .2%,100% 1.4%,100% 98.4%,88% 99.7%,74% 98.5%,58% 99.8%,42% 98.6%,26% 99.7%,12% 98.5%,4% 99.8%,0 98.7%)}
.support-title{left:112px;top:2870px;font-size:44px;color:var(--white)}
.support-text{left:112px;top:2936px;width:466px;font-size:15.5px;line-height:25.5px;color:var(--white)}
.pill{position:absolute;width:223px;height:58px;border-radius:6px;background:rgba(255,255,255,.18);display:flex;align-items:center;justify-content:center;color:var(--white);font-family:"Outfit",sans-serif;font-weight:500;font-size:16px}
.support-btn{left:110px;top:3178px;width:134px;height:52px;background:var(--white);color:var(--red)}
.support-photo{left:684px;top:2895px;width:356px;height:350px;border-radius:50% 50% 12px 12px;background:radial-gradient(circle at 50% 50%,#f1ebe0 0%,#c9c4bc 40%,#2a2a2c 62%,#1a1a1b 100%);opacity:.95}

/* footer */
.footer-brand{left:0;top:3400px;width:1200px;justify-content:center;font-size:50px;letter-spacing:1px}
.footer-brand .brand-dot{width:40px;height:40px}
.footer-nav{left:0;top:3498px;width:1200px;display:flex;justify-content:center;gap:34px;font-size:15px;color:#333}
.footer-contact{left:0;top:3548px;width:1200px;display:flex;justify-content:center;align-items:center;gap:16px;font-size:15px;color:#333}
.footer-contact .bar{width:1px;height:16px;background:#bbb}
.footer-contact span{display:flex;align-items:center;gap:10px}
.footer-social{left:0;top:3602px;width:1200px;display:flex;justify-content:center;gap:32px}
.footer-social i{display:block;width:16px;height:16px;border-radius:50%;background:#d8292c}
.copyright{left:0;top:3650px;width:1200px;text-align:center;font-size:14.5px;color:#333}
</style>
</head>
<body>

<header class="abs site-header">
  <div class="abs brand"><span class="brand-dot"></span>BRASAVO</div>
  <nav class="abs main-nav">
    <span class="active">Home</span><span>About us</span><span>Product Portfolio</span><span>Socials</span><span>Support</span><span>Contact</span>
  </nav>
  <div class="abs cart-count">(0)</div>
  <svg class="abs cart" viewBox="0 0 20 16"><path d="M0 1h3l3 9h10l3-7H5" fill="none" stroke="#ee6a24" stroke-width="2"/><circle cx="7" cy="14" r="1.6" fill="#ee6a24"/><circle cx="15" cy="14" r="1.6" fill="#ee6a24"/></svg>
  <div class="abs sep"></div>
  <svg class="abs search" width="18" height="18" viewBox="0 0 18 18"><circle cx="7.5" cy="7.5" r="5.5" fill="none" stroke="#ee6a24" stroke-width="2.4"/><path d="M12 12l4.5 4.5" stroke="#ee6a24" stroke-width="2.6"/></svg>
</header>

<section class="abs hero" role="img" aria-label="Open charcoal grill with flames and a raised lid, dark background"></section>
<div class="abs heading hero-welcome">Welcome to</div>
<div class="abs heading hero-title">Brasavo</div>
<div class="btn hero-btn">GET STARTED</div>

<div class="abs about-ring"></div>
<div class="abs about-photo" role="img" aria-label="Man grilling outdoors at a garden party"></div>
<h2 class="abs heading about-title">About Us</h2>
<p class="abs about-text">Lorem ipsum dolor sit amet, consectetur adipiscing elit, sed do eiusmod tempor incididunt ut labore et dolore magna aliqua. Ut enim ad minim veniam, quis nostrud exercitation ullamco laboris nisi ut aliquip ex ea commodo consequat. Duis aute irure dolor in reprehenderit in voluptate velit esse cillum dolore eu fugiat nulla pariatur. Excepteur sint occaecat cupidatat non proident, sunt in culpa qui officia est laborum.</p>
<div class="btn about-btn">GET STARTED</div>

<section class="abs portfolio" role="img" aria-label="Warm orange and red grilling background"></section>
<h2 class="abs heading portfolio-title">Product Portfolio</h2>
<div class="tile" style="left:113px;top:1467px"><div class="tile-img tool-silver" role="img" aria-label="Grill spatula"></div></div>
<div class="tile" style="left:446px;top:1467px"><div class="tile-img tool-silver" role="img" aria-label="Grill fork"></div></div>
<div class="tile" style="left:779px;top:1467px"><div class="tile-img tool-silver" role="img" aria-label="Spatula close-up"></div></div>
<div class="tile" style="left:113px;top:1748px"><div class="tile-img tool-dark" role="img" aria-label="Ceramic kamado grill with open lid"></div></div>
<div class="tile" style="left:446px;top:1748px"><div class="tile-img tool-dark" role="img" aria-label="Kamado grill detail"></div></div>
<div class="tile" style="left:779px;top:1748px"><div class="tile-img tool-silver" role="img" aria-label="Aluminium tool case"></div></div>
<div class="btn view-btn">VIEW ALL</div>

<h2 class="abs heading socials-title">Our Socials</h2>
<article class="post" style="left:111px">
  <div class="post-img" style="background:linear-gradient(135deg,#f2efe9,#c7c2b8)" role="img" aria-label="Hand holding a phone"></div>
  <div class="post-icon"></div>
  <div class="post-name">Reed Calder</div>
  <p class="post-text">Lorem ipsum dolor sit amet,<br>consectetur adipiscing</p>
  <div class="post-meta"><div class="avatar" role="img" aria-label="Author avatar"></div><span class="ago">38 Ago</span></div>
</article>
<article class="post" style="left:358px">
  <div class="post-img" style="background:linear-gradient(135deg,#3b4d5a,#a0522d)" role="img" aria-label="Skewers on a grill at night"></div>
  <div class="post-icon filled"></div>
  <div class="post-name">Reed Calder</div>
  <p class="post-text">Lorem ipsum dolor sit amet,<br>consectetur adipiscing</p>
  <div class="post-meta"><div class="avatar" role="img" aria-label="Author avatar"></div><span class="ago">38 Ago</span></div>
</article>
<article class="post" style="left:605px">
  <div class="post-img" style="background:linear-gradient(180deg,#6f8f3f,#e2732a 50%,#2b3a1d)" role="img" aria-label="Kettle grill with flames in a garden"></div>
  <div class="post-icon"></div>
  <div class="post-name">Reed Calder</div>
  <p class="post-text">Lorem ipsum dolor sit amet,<br>consectetur adipiscing</p>
  <div class="post-meta"><div class="avatar" role="img" aria-label="Author avatar"></div><span class="ago">38 Ago</span></div>
</article>
<article class="post" style="left:852px">
  <div class="post-img" style="background:linear-gradient(135deg,#9bb56a,#5d7a3a)" role="img" aria-label="Family barbecue outdoors"></div>
  <div class="post-icon filled"></div>
  <div class="post-name">Reed Calder</div>
  <p class="post-text">Lorem ipsum dolor sit amet,<br>consectetur adipiscing</p>
  <div class="post-meta"><div class="avatar" role="img" aria-label="Author avatar"></div><span class="ago">38 Ago</span></div>
</article>

<section class="abs support"></section>
<h2 class="abs heading support-title">Our Support</h2>
<p class="abs support-text">Lorem ipsum dolor sit amet, consectetur adipiscing elit, sed do eiusmod tempor incididunt ut labore et dolore magna aliqua.</p>
<div class="pill" style="left:374px;top:3020px">Lorem ipsum dolor sit</div>
<div class="pill" style="left:109px;top:3081px">Lorem ipsum dolor sit</div>
<div class="pill" style="left:374px;top:3142px">Lorem ipsum dolor sit</div>
<div class="btn support-btn">SUPPORT</div>
<div class="abs support-photo" role="img" aria-label="Front view of a ceramic kamado grill"></div>

<footer>
  <div class="abs brand footer-brand"><span class="brand-dot"></span>BRASAVO</div>
  <nav class="abs footer-nav"><span>Home</span><span>About us</span><span>Product Portfolio</span><span>Socials</span><span>Support</span><span>Contact</span></nav>
  <div class="abs footer-contact">
    <span><svg width="14" height="14" viewBox="0 0 14 14"><path d="M3 1l3 3-1.5 1.5a8 8 0 0 0 4 4L10 8l3 3-2 2C6 13 1 8 1 3z" fill="#ee6a24"/></svg>+1 (555) 014 2290</span>
    <i class="bar"></i>
    <span><svg width="15" height="11" viewBox="0 0 15 11"><rect width="15" height="11" rx="1" fill="#ee6a24"/><path d="M1 1l6.5 5L14 1" fill="none" stroke="#fff" stroke-width="1.2"/></svg>info@brasavo.com</span>
    <i class="bar"></i>
    <span><svg width="12" height="16" viewBox="0 0 12 16"><path d="M6 0a6 6 0 0 0-6 6c0 4.5 6 10 6 10s6-5.5 6-10a6 6 0 0 0-6-6z" fill="#ee6a24"/><circle cx="6" cy="6" r="2.2" fill="#fff"/></svg>Lorem ipsum dolor sit amet,</span>
  </div>
  <div class="abs footer-social"><i></i><i></i><i></i><i></i></div>
  <div class="abs copyright">Copyrights 2023 Brasavo &nbsp;|&nbsp;&nbsp; All Rights Reserved</div>
</footer>

</body>
</html>
```